BOLD & MINIMALIST DESIGN NEEDED

We want a very bold but minimalistic business card design that is impactful and utilizes both sides of the business card. Our current logo is included for your use.

We want bold fonts and good use of negative space. We don't want the logo to overpower the design.

Target Market(s)

Professionals who are building new commercial buildings.

Industry/Entity Type

Construction

Contact Information for Business Card

Name, Title, email, office phone, cell phone, website

Font styles to use
Serif
Sans Serif

Requirements
Must have
• Bold design!

```html
<!DOCTYPE html>
<html lang="en">
<head>
<meta charset="utf-8">
<title>Ridgeline Business Card</title>
<link rel="stylesheet" href="https://fonts.googleapis.com/css2?family=Poppins:wght@400;600;700&display=swap">
<style>
  :root {
    --page-bg: #e6e2dc;
    --card-top: #f4f6f8;
    --card-bottom: #dde2e6;
    --ink: #161616;
    --panel-dark: #1b1b1b;
    --brand-green: #4c9a2a;
    --contact-text: #cfcac4;
  }
  * { margin: 0; padding: 0; box-sizing: border-box; }
  html, body { width: 1200px; height: 970px; overflow: hidden; }
  body {
    background: var(--page-bg);
    font-family: "Poppins", sans-serif;
    position: relative;
  }
  .business-card {
    position: absolute;
    left: 50px;
    top: 172px;
    width: 1100px;
    height: 626px;
    border-radius: 30px;
    overflow: hidden;
    background: linear-gradient(160deg, var(--card-top) 0%, var(--card-bottom) 100%);
    box-shadow: 0 18px 40px rgba(0,0,0,0.18);
  }
  .card-artwork {
    position: absolute;
    inset: 0;
    background: linear-gradient(165deg, transparent 47%, var(--panel-dark) 56%);
  }
  .brand-name {
    position: absolute;
    left: 70px;
    top: 240px;
    display: flex;
    align-items: center;
    gap: 18px;
    font-weight: 700;
    font-size: 60px;
    letter-spacing: 1px;
    color: var(--ink);
  }
  .brand-square {
    width: 40px;
    height: 40px;
    background: var(--brand-green);
  }
  .holder {
    position: absolute;
    right: 63px;
    top: 82px;
    text-align: right;
  }
  .holder-name {
    font-weight: 700;
    font-size: 40px;
    line-height: 1.1;
    color: var(--ink);
  }
  .holder-title {
    font-weight: 400;
    font-size: 27px;
    color: var(--brand-green);
  }
  .address {
    position: absolute;
    right: 63px;
    top: 366px;
    text-align: right;
    font-size: 24px;
    line-height: 35px;
    color: var(--contact-text);
  }
  .contact-list {
    position: absolute;
    right: 63px;
    top: 458px;
    list-style: none;
  }
  .contact-item {
    display: flex;
    justify-content: flex-end;
    align-items: center;
    gap: 12px;
    height: 35px;
    font-size: 24px;
    color: var(--contact-text);
  }
  .contact-icon {
    width: 28px;
    height: 28px;
    flex: none;
  }
</style>
</head>
<body>
  <div class="business-card">
    <div class="card-artwork" role="img" aria-label="Decorative dark swoosh artwork with green accent across the lower card"></div>

    <div class="brand-name"><span class="brand-square"></span>RIDGELINE</div>

    <div class="holder">
      <div class="holder-name">NOAH FLETCHER</div>
      <div class="holder-title">Consultant</div>
    </div>

    <div class="address">
      <div>PO BOX 418, Harbour Road</div>
      <div>5th street, Geelong</div>
    </div>

    <ul class="contact-list">
      <li class="contact-item">0400 555 210
        <svg class="contact-icon" viewBox="0 0 28 28" aria-hidden="true">
          <circle cx="14" cy="14" r="13" fill="var(--brand-green)"/>
          <path d="M9 8 L12 8 L13 11 L11.5 12.5 C12.5 14.5 13.5 15.5 15.5 16.5 L17 15 L20 16 L20 19 C14 20 8 14 9 8 Z" fill="var(--panel-dark)"/>
        </svg>
      </li>
      <li class="contact-item">hello@ridgelinebuild.com
        <svg class="contact-icon" viewBox="0 0 28 28" aria-hidden="true">
          <circle cx="14" cy="14" r="13" fill="var(--brand-green)"/>
          <rect x="7.5" y="9.5" width="13" height="9" fill="var(--panel-dark)"/>
          <path d="M7.5 9.5 L14 15 L20.5 9.5" fill="none" stroke="var(--brand-green)" stroke-width="1.4"/>
        </svg>
      </li>
      <li class="contact-item">www.ridgelinebuild.com
        <svg class="contact-icon" viewBox="0 0 28 28" aria-hidden="true">
          <circle cx="14" cy="14" r="13" fill="var(--brand-green)"/>
          <g fill="none" stroke="var(--panel-dark)" stroke-width="1.6">
            <circle cx="14" cy="14" r="7"/>
            <ellipse cx="14" cy="14" rx="3" ry="7"/>
            <path d="M7 14 H21"/>
          </g>
        </svg>
      </li>
    </ul>
  </div>
</body>
</html>
```